Business Card Design Project

Business card based on attached logo

Todd Merrick
Todd@lorvantest.com
877-514-9073 ext. 318
Www.LorvanTest.com

Industry/Entity Type

Business

```html
<!DOCTYPE html>
<html lang="en">
<head>
<meta charset="utf-8">
<title>LorvanTest Business Cards</title>
<link rel="stylesheet" href="https://fonts.googleapis.com/css2?family=Arimo:wght@400;700&display=swap">
<style>
  :root {
    --backdrop: #898c8f;
    --card-light: #f1f1f1;
    --card-light-edge: #d9d9d9;
    --brand-red: #e0242b;
    --brand-red-deep: #b81c24;
    --ink: #1d1d1d;
    --ink-soft: #2a2a2a;
    --white: #ffffff;
  }
  * { box-sizing: border-box; margin: 0; padding: 0; }
  html, body { width: 1200px; height: 720px; overflow: hidden; }
  body {
    background: var(--backdrop);
    font-family: "Arimo", Arial, sans-serif;
    position: relative;
  }
  .card {
    position: absolute;
    width: 565px;
    height: 322px;
    overflow: hidden;
  }
  .card--contact { left: 28px; top: 25px; background: linear-gradient(100deg, var(--card-light) 30%, var(--card-light-edge)); }
  .card--red { left: 612px; top: 25px; background: linear-gradient(135deg, #e4262d, var(--brand-red-deep)); }
  .card--light { left: 28px; top: 372px; background: linear-gradient(100deg, #e3e3e3, #f4f4f4 45%, #dcdcdc); }
  .card--dark { left: 612px; top: 372px; background: radial-gradient(ellipse at 50% 40%, #3a3a3a, #1c1c1c 75%); }

  .swoosh { position: absolute; inset: 0; }

  .wordmark {
    font-weight: 700;
    letter-spacing: -1px;
    display: flex;
    align-items: center;
    gap: 12px;
    line-height: 1;
  }
  .wordmark__square { display: block; background: var(--brand-red); }

  .card--contact .wordmark { position: absolute; left: 40px; top: 90px; font-size: 52px; color: var(--ink); }
  .card--contact .wordmark__square { width: 26px; height: 26px; }
  .holder-name {
    position: absolute; left: 48px; top: 253px;
    color: var(--brand-red); font-size: 20px; font-weight: 400; text-transform: uppercase;
  }
  .contact-list {
    position: absolute; right: 15px; top: 253px;
    list-style: none; text-align: right; color: var(--white); font-size: 16px; line-height: 25px;
  }
  .contact-list li { display: flex; justify-content: flex-end; align-items: center; gap: 6px; }
  .contact-list svg { width: 12px; height: 12px; }

  .card--red .wordmark { position: absolute; left: 36px; top: 45px; font-size: 82px; color: var(--white); }
  .card--red .faint-square {
    position: absolute; left: 490px; top: 178px; width: 80px; height: 80px;
    background: rgba(255,255,255,0.13);
  }

  .site {
    position: absolute; letter-spacing: 3px; font-size: 17px; font-weight: 400;
  }
  .card--red .site { left: 36px; top: 300px; color: var(--white); }
  .card--light .site { left: 0; right: 0; text-align: center; top: 290px; color: var(--ink-soft); }
  .card--dark .site { left: 0; right: 0; text-align: center; top: 290px; color: var(--white); }

  .card--light .brand-square {
    position: absolute; left: 211px; top: 51px; width: 143px; height: 143px; background: #ee3a3e;
  }

  .card--dark .wordmark {
    position: absolute; left: 0; right: 0; justify-content: center; top: 112px; font-size: 70px; color: var(--white);
  }
  .card--dark .wordmark__square { width: 30px; height: 30px; }
  .card--red .wordmark__square { width: 34px; height: 34px; background: var(--white); }
</style>
</head>
<body>
  <section class="card card--contact">
    <svg class="swoosh" viewBox="0 0 565 322" preserveAspectRatio="none" aria-hidden="true">
      <defs>
        <linearGradient id="swooshRed" x1="0" y1="1" x2="1" y2="0">
          <stop offset="0" stop-color="#e3242b"/>
          <stop offset="1" stop-color="#a81a22"/>
        </linearGradient>
      </defs>
      <path d="M505 0 C565 115 430 285 165 322 L565 322 L565 0 Z" fill="#222"/>
      <path d="M545 0 C590 125 470 292 205 322 L565 322 L565 0 Z" fill="url(#swooshRed)"/>
    </svg>
    <div class="wordmark"><span>LorvanTest</span><span class="wordmark__square"></span></div>
    <p class="holder-name">Todd Merrick</p>
    <ul class="contact-list">
      <li><svg viewBox="0 0 12 12"><circle cx="6" cy="6" r="5.5" fill="#fff"/><path d="M3.5 3.5h1.5l.6 1.5-.8.6a4 4 0 0 0 1.6 1.6l.6-.8 1.5.6v1.5c-3 0-5-2-5-5z" fill="#c01f26"/></svg>877-514-9073 ext. 318</li>
      <li><svg viewBox="0 0 12 12"><circle cx="6" cy="6" r="5.5" fill="#fff"/><rect x="3" y="4" width="6" height="4" fill="none" stroke="#c01f26"/><path d="M3 4l3 2.2L9 4" fill="none" stroke="#c01f26"/></svg>Todd@lorvantest.com</li>
      <li><svg viewBox="0 0 12 12"><circle cx="6" cy="6" r="5" fill="none" stroke="#fff"/><ellipse cx="6" cy="6" rx="2" ry="5" fill="none" stroke="#fff"/><path d="M1 6h10" stroke="#fff"/></svg>www.lorvantest.com</li>
    </ul>
  </section>

  <section class="card card--red">
    <div class="wordmark"><span>LorvanTest</span><span class="wordmark__square"></span></div>
    <span class="faint-square"></span>
    <p class="site">www.lorvantest.com</p>
  </section>

  <section class="card card--light">
    <span class="brand-square"></span>
    <p class="site">www.lorvantest.com</p>
  </section>

  <section class="card card--dark">
    <div class="wordmark"><span>LorvanTest</span><span class="wordmark__square"></span></div>
    <p class="site">www.lorvantest.com</p>
  </section>
</body>
</html>
```